Web Design Project - Shipping Industry

Goals and Objectives
The objective of the new website is to create a more modern look and feel. The site will also allow for a more effective means of communicating with members while providing the public with information and developments in the local, regional and international shipping industry.
Scope
The website will highlight the history of the organisation inclusive of text and photographs. It will take visitors through the years from beginning to present. Information on the history of the shipping industry will also be included.
It will feature current articles on the organisation, its members and stakeholders in the shipping industry. Member information as well as pertinent details regarding the organisation’s subsidiaries will be documented for the website.
Information as it relates to shipping statistics, case studies, laws and regulations, international treaties and trade documents, shipping terms, careers in shipping, job opportunities, training opportunities, information for shippers including port listing and trade lanes will be main features of the content for the website.
The Association’s community involvement, industry calendar events and related links relevant industry members will also be featured.
Target Market
• The General Public;
• Members of the organization;
• Shipping Industry Stakeholders (local, regional and international);
• Tertiary students conducting research.
• Potential employees
• Potential Business Partners
Best Practice Bench Marketing
The following websites are being looked at:
• Korvel Quayworks - http://www.korvelquayworks.example/ (preferred look)
• Tessaly Maritime Association - http://www.tma-freight.example/ (like image transition on main page)
• Drovna - http://www.drovna.example (professional look)
• PLW - http://www.pelworth.example (preferred color: blue in logo)
• Quillo - http://www.quillo.example/electronics/tv-video-audio/ (preferred look for links page: image + short text below + visit site link)
Expected Result
• 3 - 5 pages which must include: [1] main page [2] standard page [3] links page

```html
<!DOCTYPE html>
<html lang="en">
<head>
<meta charset="utf-8">
<title>Navorin – Links</title>
<link href="https://fonts.googleapis.com/css2?family=PT+Sans:wght@400;700&family=Jura:wght@500;700&display=swap" rel="stylesheet">
<style>
:root{
  --page-grey:#e8e8e8;
  --paper:#ffffff;
  --ink:#111111;
  --brand:#2d2a5c;
  --link-blue:#1f4fbf;
  --nav-top:#3f72d9;
  --nav-mid:#1a3f99;
  --nav-bottom:#00205e;
  --accent-gold:#f1c232;
  --line:#d6d6d6;
}
*{box-sizing:border-box;margin:0;padding:0}
html,body{width:1040px;height:1200px;overflow:hidden}
body{
  background:linear-gradient(var(--page-grey) 0 1088px,var(--paper) 1088px);
  font-family:"PT Sans",sans-serif;color:var(--ink);position:relative;
}
.page{position:absolute;left:86px;top:0;width:864px;height:1088px;background:var(--paper)}
.account-links{position:absolute;right:35px;top:10px;font-size:13px;display:flex;gap:8px}
.account-links a{color:var(--ink);text-decoration:none}
.brand{position:absolute;left:36px;top:50px;font-family:"Jura",sans-serif;font-weight:700;font-size:26px;letter-spacing:5px;color:var(--brand)}
.social{position:absolute;left:570px;top:57px;display:flex;gap:5px}
.social span{width:12px;height:12px;background:#6b87b8;border-radius:2px;display:block}
.search{position:absolute;left:643px;top:52px;width:192px;height:22px;border:1px solid var(--line);font-size:11px;padding:4px 9px;color:#222}
.search svg{position:absolute;right:8px;top:4px}
.main-nav{position:absolute;left:35px;top:110px;width:800px;height:40px;border-top:2px solid var(--accent-gold);
  background:linear-gradient(var(--nav-top),var(--nav-mid) 45%,var(--nav-bottom) 50%,var(--nav-bottom));
  display:flex;justify-content:space-around;align-items:center;padding-bottom:8px}
.main-nav a{color:#fff;text-decoration:none;font-weight:700;font-size:10.5px;letter-spacing:.2px}
.hero{position:absolute;left:35px;top:150px;width:800px;height:196px;
  background:linear-gradient(100deg,#3a6b88 0%,#cfd3d6 30%,#5a8a6a 50%,#2f6f96 80%,#1d5a80 100%)}
.section-title{position:absolute;left:35px;top:364px;font-family:"Jura",sans-serif;font-weight:500;font-size:29px;color:var(--brand)}
.link-card{position:absolute;width:176px}
.link-card .thumb{height:88px}
.link-card h2{font-family:"Jura",sans-serif;font-weight:700;font-size:10.6px;margin:8px 0 7px;white-space:nowrap;letter-spacing:.1px}
.link-card p{font-size:9.6px;line-height:13px}
.visit{display:flex;align-items:center;gap:6px;margin-top:8px;color:var(--link-blue);font-weight:700;font-size:9.8px;text-decoration:none}
.row-2 h2{margin-top:11px}
.row-2 .visit{margin-top:12px}
.site-footer{position:absolute;left:0;top:802px;width:864px;height:38px;
  background:linear-gradient(var(--nav-top),var(--nav-mid) 45%,var(--nav-bottom) 50%,var(--nav-bottom));
  color:#fff;font-size:9px;padding:16px 35px 0;display:flex;justify-content:space-between}
.footer-links{display:flex;gap:10px;padding-right:14px}
.footer-links a{color:#fff;text-decoration:none}
</style>
</head>
<body>
<div class="page">
  <nav class="account-links"><a href="#">Register</a><span>|</span><a href="#">Login</a></nav>
  <div class="brand">NAVORIN</div>
  <div class="social" aria-hidden="true"><span></span><span></span><span></span><span></span></div>
  <div class="search">Search
    <svg width="13" height="13" viewBox="0 0 13 13"><circle cx="8" cy="5" r="3.8" fill="none" stroke="#bbb" stroke-width="1.4"/><line x1="5.3" y1="7.7" x2="1" y2="12" stroke="#bbb" stroke-width="1.8"/></svg>
  </div>
  <nav class="main-nav">
    <a href="#">HOME</a><a href="#">ABOUT US</a><a href="#">PRODUCTS</a><a href="#">SERVICES</a><a href="#">NEWS</a><a href="#">SUPPORT</a><a href="#">PARTNERS</a><a href="#">CUSTOMERS</a><a href="#">CONTACT</a>
  </nav>
  <div class="hero" role="img" aria-label="Container ship loaded with cargo cutting through the open sea"></div>
  <h1 class="section-title">LINKS</h1>

  <article class="link-card" style="left:36px;top:407px"><div class="thumb" role="img" aria-label="Container ship berthed beside red quay cranes" style="background:linear-gradient(90deg,#8a9aa8,#b7c0c6 40%,#b8302c 70%,#6d6a66)"></div><h2>PELWORTH.EXAMPLE</h2><p>Lorem ipsum dolor sit amet, consectetur adipisicing elit, sed do eiusmod tempor</p><a class="visit" href="#">VISIT WEBSITE <svg width="13" height="13" viewBox="0 0 13 13"><circle cx="6.5" cy="6.5" r="6.5" fill="var(--nav-bottom)"/><path d="M3.5 6.5h5.5M6.8 4l2.5 2.5-2.5 2.5" stroke="#fff" stroke-width="1.4" fill="none"/></svg></a></article>
  <article class="link-card" style="left:244px;top:407px"><div class="thumb" role="img" aria-label="Ship superstructure and crane against a city skyline" style="background:linear-gradient(160deg,#6fa0d6,#c9d8e8 50%,#3a72b8)"></div><h2>TIDEGATEMARINE.EXAMPLE</h2><p>Lorem ipsum dolor sit amet, consectetur adipisicing elit, sed do eiusmod tempor</p><a class="visit" href="#">VISIT WEBSITE <svg width="13" height="13" viewBox="0 0 13 13"><circle cx="6.5" cy="6.5" r="6.5" fill="var(--nav-bottom)"/><path d="M3.5 6.5h5.5M6.8 4l2.5 2.5-2.5 2.5" stroke="#fff" stroke-width="1.4" fill="none"/></svg></a></article>
  <article class="link-card" style="left:451px;top:407px"><div class="thumb" role="img" aria-label="Container vessel stern at a terminal" style="background:linear-gradient(180deg,#7fa6d0,#d7dde3 55%,#3d4e6a)"></div><h2>CARGOWELLLTD.EXAMPLE</h2><p>Lorem ipsum dolor sit amet, consectetur adipisicing elit, sed do eiusmod tempor</p><a class="visit" href="#">VISIT WEBSITE <svg width="13" height="13" viewBox="0 0 13 13"><circle cx="6.5" cy="6.5" r="6.5" fill="var(--nav-bottom)"/><path d="M3.5 6.5h5.5M6.8 4l2.5 2.5-2.5 2.5" stroke="#fff" stroke-width="1.4" fill="none"/></svg></a></article>
  <article class="link-card" style="left:658px;top:407px"><div class="thumb" role="img" aria-label="Dock workers beside a red ship hull on the quay" style="background:linear-gradient(90deg,#b5303a,#c46060 50%,#4e7fb0)"></div><h2>CARGOWELLLTD.EXAMPLE</h2><p>Lorem ipsum dolor sit amet, consectetur adipisicing elit, sed do eiusmod tempor</p><a class="visit" href="#">VISIT WEBSITE <svg width="13" height="13" viewBox="0 0 13 13"><circle cx="6.5" cy="6.5" r="6.5" fill="var(--nav-bottom)"/><path d="M3.5 6.5h5.5M6.8 4l2.5 2.5-2.5 2.5" stroke="#fff" stroke-width="1.4" fill="none"/></svg></a></article>

  <article class="link-card row-2" style="left:36px;top:596px"><div class="thumb" role="img" aria-label="Compass over a world map in blue tones" style="background:linear-gradient(135deg,#8fe0f0,#2c86b8 50%,#0c2f5c)"></div><h2>DUNESLINE.EXAMPLE</h2><p>Lorem ipsum dolor sit amet, consectetur adipisicing elit, sed do eiusmod tempor</p><a class="visit" href="#">VISIT WEBSITE <svg width="13" height="13" viewBox="0 0 13 13"><circle cx="6.5" cy="6.5" r="6.5" fill="var(--nav-bottom)"/><path d="M3.5 6.5h5.5M6.8 4l2.5 2.5-2.5 2.5" stroke="#fff" stroke-width="1.4" fill="none"/></svg></a></article>
  <article class="link-card row-2" style="left:244px;top:596px"><div class="thumb" role="img" aria-label="Loaded container ship sailing at sea" style="background:linear-gradient(150deg,#2f6e96,#9c5a48 50%,#1e5a86)"></div><h2>HARBORFREIGHTCO.EXAMPLE</h2><p>Lorem ipsum dolor sit amet, consectetur adipisicing elit, sed do eiusmod tempor</p><a class="visit" href="#">VISIT WEBSITE <svg width="13" height="13" viewBox="0 0 13 13"><circle cx="6.5" cy="6.5" r="6.5" fill="var(--nav-bottom)"/><path d="M3.5 6.5h5.5M6.8 4l2.5 2.5-2.5 2.5" stroke="#fff" stroke-width="1.4" fill="none"/></svg></a></article>
  <article class="link-card row-2" style="left:451px;top:596px"><div class="thumb" role="img" aria-label="Cargo ship with stacked containers on open water" style="background:linear-gradient(180deg,#a9c0d4,#476f8f 40%,#8a4a3c 60%,#23506f)"></div><h2>GLOBALBERTHS.EXAMPLE</h2><p>Lorem ipsum dolor sit amet, consectetur adipisicing elit, sed do eiusmod tempor</p><a class="visit" href="#">VISIT WEBSITE <svg width="13" height="13" viewBox="0 0 13 13"><circle cx="6.5" cy="6.5" r="6.5" fill="var(--nav-bottom)"/><path d="M3.5 6.5h5.5M6.8 4l2.5 2.5-2.5 2.5" stroke="#fff" stroke-width="1.4" fill="none"/></svg></a></article>
  <article class="link-card row-2" style="left:658px;top:596px"><div class="thumb" role="img" aria-label="Aerial view of a container yard" style="background:linear-gradient(135deg,#8c8a86,#a77a6c 50%,#6f7a84)"></div><h2>EURQUAY.EXAMPLE</h2><p>Lorem ipsum dolor sit amet, consectetur adipisicing elit, sed do eiusmod tempor</p><a class="visit" href="#">VISIT WEBSITE <svg width="13" height="13" viewBox="0 0 13 13"><circle cx="6.5" cy="6.5" r="6.5" fill="var(--nav-bottom)"/><path d="M3.5 6.5h5.5M6.8 4l2.5 2.5-2.5 2.5" stroke="#fff" stroke-width="1.4" fill="none"/></svg></a></article>

  <footer class="site-footer">
    <span>© HARBOR DATA SERVICES | ALL RIGHT RESERVED</span>
    <nav class="footer-links"><a href="#">LEGAL NOTICE</a><span>|</span><a href="#">PRIVACY POLICY</a><span>|</span><a href="#">CONTACT US</a></nav>
  </footer>
</div>
</body>
</html>
```